I'm looking for a smart new design for business cards

Industry/Entity Type

Commercial Electrical

Contact Information for Business Card

Logo, name, email, position, website QR

Requirements
Nice to have
• Logo embedded behind the text side

```html
<!DOCTYPE html>
<html lang="en">
<head>
<meta charset="utf-8">
<title>Northgrid Commercial Electrical – Business Card</title>
<link href="https://fonts.googleapis.com/css2?family=Montserrat:wght@700;800&family=Arimo:wght@400&display=swap" rel="stylesheet">
<style>
  :root {
    --navy: #0c0f80;
    --red: #e3173e;
    --ink: #111111;
    --grey: #555555;
    --rule: #c9c9c9;
    --paper: #ffffff;
    --backdrop: #e4e4e4;
  }
  html, body { margin: 0; padding: 0; overflow: hidden; }
  body { width: 1200px; height: 1200px; background: var(--backdrop); position: relative; }

  .card {
    position: absolute;
    width: 687px;
    height: 392px;
    border-radius: 22px;
    overflow: hidden;
  }
  .card--front { left: 267px; top: 159px; background: var(--paper); }
  .card--back  { left: 262px; top: 654px; background: var(--navy); }

  /* Front: brand block */
  .brand {
    position: absolute;
    left: 60px;
    top: 130px;
    width: 290px;
    text-align: center;
  }
  .brand__dot {
    width: 40px; height: 40px;
    border-radius: 50%;
    background: var(--red);
    margin: 0 auto 14px;
  }
  .brand__name {
    font-family: "Montserrat", sans-serif;
    font-weight: 700;
    font-size: 16px;
    line-height: 19px;
    color: var(--ink);
    letter-spacing: 0.2px;
    margin: 0;
  }

  .divider {
    position: absolute;
    left: 362px;
    top: 85px;
    width: 1.5px;
    height: 226px;
    background: var(--rule);
  }

  .contact { position: absolute; left: 387px; top: 94px; }
  .contact__name {
    font-family: "Montserrat", sans-serif;
    font-weight: 800;
    font-size: 26px;
    color: var(--navy);
    margin: 0;
    line-height: 30px;
  }
  .contact__role {
    font-family: "Arimo", sans-serif;
    font-size: 16px;
    color: var(--red);
    margin: 1px 0 0;
  }
  .contact__address {
    font-family: "Arimo", sans-serif;
    font-size: 16px;
    line-height: 21px;
    color: var(--grey);
    margin: 20px 0 0;
  }
  .contact__list { list-style: none; margin: 12px 0 0; padding: 0; }
  .contact__item {
    font-family: "Arimo", sans-serif;
    font-size: 16px;
    color: var(--grey);
    height: 20.5px;
    display: flex;
    align-items: center;
  }
  .contact__icon { width: 14px; height: 14px; margin-right: 11px; flex: none; }

  /* Back */
  .back__map {
    position: absolute;
    left: 108px; top: 13px;
    width: 444px; height: 372px;
    background: var(--paper);
    border-radius: 60px 90px 80px 120px;
  }
  .back__name {
    position: absolute;
    left: 0; right: 0;
    top: 156px;
    margin: 0;
    text-align: center;
    font-family: "Montserrat", sans-serif;
    font-weight: 700;
    font-size: 24px;
    line-height: 29px;
    color: var(--navy);
    letter-spacing: 0.3px;
  }
</style>
</head>
<body>

<section class="card card--front" aria-label="Business card front">
  <div class="brand">
    <div class="brand__dot"></div>
    <p class="brand__name">NORTHGRID COMMERCIAL<br>ELECTRICAL</p>
  </div>

  <div class="divider"></div>

  <div class="contact">
    <h1 class="contact__name">DANIEL REYES</h1>
    <p class="contact__role">President</p>
    <p class="contact__address">4120 Harbor View Road<br>Millbrook, Canada 20418</p>
    <ul class="contact__list">
      <li class="contact__item">
        <svg class="contact__icon" viewBox="0 0 14 14"><path fill="#e3173e" d="M3 1l2.2 2.6-1.2 1.6c.8 1.8 2.4 3.4 4.2 4.2l1.6-1.2L12.4 10.4 11 13C5.8 12.6 1.4 8.2 1 3z"/></svg>
        555-214-0187
      </li>
      <li class="contact__item">
        <svg class="contact__icon" viewBox="0 0 14 14"><rect x="3.5" y="0.8" width="7" height="12.4" rx="1.2" fill="none" stroke="#e3173e" stroke-width="1.6"/><circle cx="7" cy="10.8" r="0.9" fill="#e3173e"/></svg>
        555-309-7742
      </li>
      <li class="contact__item">
        <svg class="contact__icon" viewBox="0 0 14 14"><rect x="1" y="3" width="12" height="8.5" fill="#e3173e"/><path d="M1.5 3.5L7 8l5.5-4.5" fill="none" stroke="#fff" stroke-width="1.2"/></svg>
        info@northgrid.com
      </li>
      <li class="contact__item">
        <svg class="contact__icon" viewBox="0 0 14 14"><circle cx="7" cy="7" r="6" fill="#e3173e"/><path d="M4 4.5c1.2.2 2 1 1.8 2.2L7.5 8 6.8 11M9 2.8c-.6 1.2.2 2 1.4 2" fill="none" stroke="#fff" stroke-width="1.1"/></svg>
        www.northgrid.com
      </li>
    </ul>
  </div>
</section>

<section class="card card--back" aria-label="Business card back">
  <div class="back__map" role="img" aria-label="White map silhouette of Australia"></div>
  <p class="back__name">NORTHGRID COMMERCIAL<br>ELECTRICAL</p>
</section>

</body>
</html>
```